Brochure condensed from the PDF marketing

An organised brochure with 4 x banner heading for the various portfolios,
Condensed and made into a 4 page booklet or neat and tidy brochure display that can be easily emailed to prospective customers. The brochure should be neat and professional similar content to the website to send the 4 x Portfolios to the various Industry Categories, thank you

** Ive just uploaded a couple of extra photos for the ' Our Services ' area on the Brochure, pls add the ice cream one for the ' Parfait Cleaning and Sanitisation Services, and on the ' Our Services' category for the High pressure Gurney and Playground Cleaning pls add a fun photo for example the one I sent with people having fun on the playground equipment, **

HI KT Designer The brochure design is for my facebook title page /Users/user/Desktop/Screenshot 2020-05-05 at 9.22.39 PM.png Under Brightwell Facebook Design (Contest) DO you have a direct email, its very difficult to keep posing images and updates here Thank you Imogen @ Brightwell.

Target Market(s)

Cleaning Services

Font styles to use
Serif

Requirements
Must have
• Look professional and neat and tidy brochure booklet for marketing on email to prospective customers.

```html
<!DOCTYPE html>
<html lang="en">
<head>
<meta charset="utf-8">
<title>Brightwell Brochure</title>
<link rel="stylesheet" href="https://fonts.googleapis.com/css2?family=Roboto+Slab:wght@400;600;700&family=Open+Sans:wght@400;600;700&display=swap">
<style>
:root{
  --navy:#16427f;
  --navy-deep:#103a70;
  --orange:#ef5a1f;
  --paper:#f4f4f5;
  --ink:#1f3260;
  --stage:#d8d8d9;
  --white:#ffffff;
  --slab:"Roboto Slab", Georgia, serif;
  --sans:"Open Sans", Arial, sans-serif;
}
*{box-sizing:border-box;margin:0;padding:0}
html,body{width:904px;height:1200px;overflow:hidden}
body{background:var(--stage);position:relative;font-family:var(--sans);color:var(--ink)}
.spread{position:absolute;left:42px;width:820px;height:560px;display:flex;box-shadow:0 6px 18px rgba(0,0,0,.18)}
.spread--outside{top:30px}
.spread--inside{top:615px}
.page{position:relative;width:410px;height:560px;overflow:hidden;background:var(--paper)}

/* brand name */
.brand{display:flex;align-items:center;gap:7px;font-family:var(--slab);font-weight:400;color:var(--orange);line-height:1}
.brand-dot{border-radius:50%;background:var(--navy)}

/* back cover */
.back{background:var(--navy)}
.back .brand{position:absolute;top:86px;left:0;right:0;justify-content:center;font-size:30px;color:var(--white)}
.back .brand-dot{width:22px;height:22px;background:var(--orange)}
.back-contact{position:absolute;top:132px;left:0;right:0;text-align:center;font-family:var(--slab);color:var(--white);font-size:11.5px;line-height:1.5}

/* front cover */
.front .brand{position:absolute;top:30px;left:0;right:0;justify-content:center;font-size:32px}
.front .brand-dot{width:26px;height:26px}
.front-rule{position:absolute;top:80px;left:20px;right:20px;height:3px;background:var(--orange)}
.cover-grid{position:absolute;top:92px;left:20px;width:370px;height:300px;display:grid;grid-template-columns:1fr 1fr;grid-template-rows:1fr 1fr;gap:3px}
.cover-tile{position:relative}
.cover-tile .photo{position:absolute;inset:0}
.tile-label{position:absolute;left:0;right:0;bottom:10px;background:var(--orange);color:var(--white);padding:5px 10px;font-family:var(--sans);font-size:9px;line-height:1.15;letter-spacing:.2px}
.tile-label strong{display:block;font-size:10px;font-weight:700}
.tile-label--right{text-align:right}
.welcome{position:absolute;top:420px;left:0;right:20px;text-align:right;font-family:var(--slab)}
.welcome-lead{font-size:30px;color:var(--navy);line-height:1}
.welcome-name{font-size:44px;font-weight:700;color:var(--orange);line-height:1.05;letter-spacing:.5px}
.welcome-url{font-size:12px;color:var(--ink);margin-top:6px}

/* photo placeholders */
.photo{display:block}
.photo--sink{background:linear-gradient(135deg,#8a8f95,#c79a62)}
.photo--kitchen{background:linear-gradient(135deg,#9fc2d4,#5b7f95)}
.photo--playground{background:linear-gradient(135deg,#6f9a52,#3fa27a)}
.photo--pressure{background:linear-gradient(135deg,#5f7a4a,#a65a4a)}
.photo--carpet{background:linear-gradient(160deg,#9aa2ab,#5977a8)}
.photo--windows{background:linear-gradient(135deg,#7da6c9,#3b6f9c)}
.photo--team{background:linear-gradient(135deg,#d7b7a4,#8e6d62)}

/* inside left */
.intro-photo{position:absolute;top:18px;left:0;width:150px;height:200px;border-radius:0 80px 80px 0}
.intro{position:absolute;top:28px;left:166px;width:226px}
.section-title{font-family:var(--slab);font-weight:700;color:var(--navy);font-size:15px;line-height:1;text-transform:uppercase}
.section-title em{font-style:normal;color:var(--orange)}
.intro .section-title{margin-bottom:8px}
.body-copy{font-size:6.8px;line-height:1.5;color:var(--ink);margin-bottom:6px}
.pillars{position:absolute;top:228px;left:18px;width:374px;height:208px;display:grid;grid-template-columns:repeat(3,1fr);gap:4px}
.pillar{background:var(--navy);color:var(--white);text-align:center;display:flex;flex-direction:column}
.pillar-head{background:var(--orange);height:62px;display:flex;align-items:center;justify-content:center}
.pillar-title{font-family:var(--slab);font-size:11px;font-weight:600;margin:10px 0 6px;text-transform:uppercase}
.pillar-text{font-size:6.6px;line-height:1.5;padding:0 10px}
.values{position:absolute;top:446px;left:18px;width:380px}
.values .section-title{margin-bottom:5px}
.values-list{list-style:none;font-size:6.4px;line-height:1.55}
.values-list b{color:var(--navy)}
.page-foot{position:absolute;bottom:16px;left:18px;right:18px;display:flex;align-items:center;gap:10px}
.page-foot .brand{font-size:16px}
.page-foot .brand-dot{width:13px;height:13px}
.foot-rule{flex:1;height:1px;background:var(--navy)}
.page-num{width:16px;height:16px;background:var(--orange);color:var(--white);font-family:var(--slab);font-size:9px;font-weight:700;display:flex;align-items:center;justify-content:center}

/* inside right */
.services{position:absolute;top:22px;left:14px;right:14px;text-align:center}
.services .section-title{margin-bottom:12px}
.service-row{display:grid;grid-template-columns:repeat(4,1fr);gap:6px}
.service-photo{width:68px;height:68px;border-radius:50%;margin:0 auto 7px;border:3px solid var(--white);box-shadow:0 1px 3px rgba(0,0,0,.2)}
.service-name{font-family:var(--slab);font-weight:600;color:var(--navy);font-size:8px;line-height:1.25}
.safety{position:absolute;top:182px;left:0;right:0;height:170px;background:var(--navy);color:var(--white);text-align:center;padding:16px 28px}
.safety .section-title{color:var(--white);margin-bottom:8px}
.safety .body-copy{color:var(--white)}
.staff{position:absolute;top:366px;left:22px;right:22px}
.staff .section-title{margin-bottom:7px}
</style>
</head>
<body>

<section class="spread spread--outside">
  <article class="page back">
    <div class="brand"><span class="brand-dot"></span>Brightwell</div>
    <address class="back-contact">
      Sydney | Brisbane | Melbourne | Adelaide<br>
      Australia ABN 48 902 315 660<br>
      Landline: 1300 555 014<br>
      Mobile: 0400 555 218<br>
      Email: service@brightwell.example<br>
      www.brightwell.example
    </address>
  </article>

  <article class="page front">
    <div class="brand"><span class="brand-dot"></span>Brightwell</div>
    <div class="front-rule"></div>
    <div class="cover-grid">
      <div class="cover-tile">
        <span class="photo photo--sink" role="img" aria-label="Hands scrubbing a wooden chopping board under a kitchen tap"></span>
        <p class="tile-label">FOOD SERVICE EQUIPMENT<strong>CLEANING</strong></p>
      </div>
      <div class="cover-tile">
        <span class="photo photo--playground" role="img" aria-label="Children playing with a bucket of water in a park"></span>
        <p class="tile-label tile-label--right">PLAYGROUND<strong>CLEANING</strong></p>
      </div>
      <div class="cover-tile">
        <span class="photo photo--kitchen" role="img" aria-label="Stainless steel commercial restaurant kitchen"></span>
        <p class="tile-label">COMMERCIAL RESTAURANT<strong>CLEANING</strong></p>
      </div>
      <div class="cover-tile">
        <span class="photo photo--pressure" role="img" aria-label="Worker pressure washing a paved path"></span>
        <p class="tile-label tile-label--right">HIGH PRESSURE WATER<strong>CLEANING</strong></p>
      </div>
    </div>
    <div class="welcome">
      <p class="welcome-lead">Welcome to</p>
      <p class="welcome-name">BRIGHTWELL</p>
      <p class="welcome-url">www.brightwell.example</p>
    </div>
  </article>
</section>

<section class="spread spread--inside">
  <article class="page inside-left">
    <span class="photo photo--carpet intro-photo" role="img" aria-label="Technician in overalls and shoe covers cleaning carpet"></span>
    <div class="intro">
      <h2 class="section-title">Working<br>with <em>Brightwell</em></h2>
      <p class="body-copy">We are Brightwell, a leading, Australian owned, cleaning services company.</p>
      <p class="body-copy">When you work with Brightwell it is easy to do business with us.</p>
      <p class="body-copy">Our people are professional, reliable and service oriented. In every interaction you have; on site, receiving help from our service support staff, or rolling-out new cleaning sites, you will see and feel the benefits of using Brightwell. The pride we take in our work and a prevailing focus on employees, customers and partners, delivers a consistent and superior ongoing service.</p>
    </div>

    <div class="pillars">
      <div class="pillar">
        <div class="pillar-head"><span role="img" aria-label="Small potted bonsai icon" style="display:block;width:30px;height:36px;background:#f8b79a;border-radius:4px"></span></div>
        <h3 class="pillar-title">Our Purpose</h3>
        <p class="pillar-text">To support and extend the life of equipment, maximize product yield and achieve high quality hygiene standards for our food and equipment service clients. We deliver this by ensuring every person in our service chain delivers their work focusing on high quality and reliable cleaning standards.</p>
      </div>
      <div class="pillar">
        <div class="pillar-head">
          <svg width="40" height="40" viewBox="0 0 40 40" aria-hidden="true"><polygon points="20,2 23,17 38,20 23,23 20,38 17,23 2,20 17,17" fill="#fff"/></svg>
        </div>
        <h3 class="pillar-title">Our Vision</h3>
        <p class="pillar-text">A sustainable food service and equipment cleaning company that creates value for customers, supports its employees in work and life and gives back to the community – now and for generations to come.</p>
      </div>
      <div class="pillar">
        <div class="pillar-head">
          <svg width="40" height="40" viewBox="0 0 40 40" aria-hidden="true"><circle cx="20" cy="20" r="17" fill="none" stroke="#fff" stroke-width="2"/><polygon points="20,7 23,20 20,33 17,20" fill="#fff"/></svg>
        </div>
        <h3 class="pillar-title">Our Strategy</h3>
        <p class="pillar-text">To differentiate ourselves through a prevailing focus on customer service, in everything we do and every interaction we have. We treat our people as skilled cleaning professionals who are the foundation of our company's sustainability.</p>
      </div>
    </div>

    <div class="values">
      <h2 class="section-title">We <em>Value</em></h2>
      <ul class="values-list">
        <li><b>Safety and the Environment</b> – We are committed to providing a safe and healthy working environment;</li>
        <li><b>Professionalism/Integrity</b> – We are committed to doing what we say we are going to do;</li>
        <li><b>Sustainability</b> – Achieving results that are mutually beneficial for our employees, our customers, our partners and the company;</li>
        <li><b>Positive Working Relationships</b> – Having relationships that focus on shared goals and creation of value for all parties;</li>
        <li><b>Respect for Each Other</b> – The embracing of diversity, enriched by openness, sharing, trust, teamwork and involvement.</li>
      </ul>
    </div>

    <footer class="page-foot">
      <div class="brand"><span class="brand-dot"></span>Brightwell</div>
      <span class="foot-rule"></span>
      <span class="page-num">1</span>
    </footer>
  </article>

  <article class="page inside-right">
    <div class="services">
      <h2 class="section-title">Our <em>Services</em></h2>
      <div class="service-row">
        <div class="service">
          <span class="photo photo--sink service-photo" role="img" aria-label="Chopping board being washed under a tap"></span>
          <p class="service-name">Equipment Cleaning &amp; Sanitisation Services</p>
        </div>
        <div class="service">
          <span class="photo photo--windows service-photo" role="img" aria-label="Window cleaners abseiling down a glass tower"></span>
          <p class="service-name">General Cleaning &amp; Property Facilities Management</p>
        </div>
        <div class="service">
          <span class="photo photo--pressure service-photo" role="img" aria-label="Pressure washing a paved area"></span>
          <p class="service-name">High Pressure gurney &amp; play ground equipment Cleaning</p>
        </div>
        <div class="service">
          <span class="photo photo--team service-photo" role="img" aria-label="Team members joining hands over a desk"></span>
          <p class="service-name">Projects and Recruiting Services Work with us</p>
        </div>
      </div>
    </div>

    <div class="safety">
      <h2 class="section-title">Safety &amp; <em>Compliance</em></h2>
      <p class="body-copy">Brightwell values safety and environment. We have an overriding commitment to health, safety and environmental responsibility.</p>
      <p class="body-copy">Each member of our company community undergoes a yearly on-line safety refresher course, and performs a routine reflection safety check and risk assessment at each clients site on attending work each day. We have safety work method statements in place and work on ensuring our people work safely on site through practical application of safety steps, safety shoes and appropriate personal protection equipment (PPE) work gear.</p>
      <p class="body-copy">Brightwell is covered with $20,000,000 General and Product Liability coverage through Harbourline Insurance Ltd and has work cover in place for all our employees across Sydney, Brisbane, Melbourne, Newcastle and Adelaide.</p>
      <p class="body-copy">Brightwell employees always aspire to work safely whilst on client sites.</p>
    </div>

    <div class="staff">
      <h2 class="section-title">Our <em>Staff</em></h2>
      <p class="body-copy">We are proud of our team. The majority of staff has been with the company for many years. As a result, the understanding of our clients and our bench strength of cleaning professionals is extremely strong.</p>
      <p class="body-copy">Our people are carefully selected from qualified trades backgrounds, or, equivalent on the job experience. They are career focused cleaning and maintenance professionals with backgrounds that include refrigeration and automobile mechanics, fitters and turners, and machinists.</p>
      <p class="body-copy">Service Technicians are provided ongoing training and development so they are always prepared for the rigors of delivering a disciplined and reliable service, including an extensive induction and buddy training system for new team members.</p>
    </div>

    <footer class="page-foot">
      <div class="brand"><span class="brand-dot"></span>Brightwell</div>
      <span class="foot-rule"></span>
      <span class="page-num">2</span>
    </footer>
  </article>
</section>

</body>
</html>
```